Scientific Web Site for KLORVEST

Professional Scientific / Service orientated web site, motto, new logos attached for viewing.

"We measure so the Business Owner can Manage" their environments.
Site needs to be be mobile friendly.

We provide a service to electronically measure cleanliness of any surface and a value added disinfecting fogging surface.

Reports showing locations, trending, tracking and randomized test plans ongoing audits will be made available..

NOTE: Although image of Corona Virus is current we don't wont it plastered through the web site, their is more than the current virus.

Home Page - Professional Scientific / Service Looking
About
Our Approach
Services
Residential
Commercial
Transportation
Gyms
Educational & Daycare
Real Estate - Open for inspections, End of Lease etc

Contact
Mobile #
Email
Form to leave their details

Links to social media, Facebook, Instagram
Reference Sites: Ranked in preference
www.brelmont.com.au
https://www.tidewellhygiene.co.uk/
https://www.mistrova.com/
https://www.zenplax.com.au/specialist-surface-disinfection/
https://www.artfolder.example/design/48172039
https://www.artfolder.example/design/51904476
https://www.artfolder.example/design/47318865

Target Market(s)

Commercial and professional Services

Font styles to use
Sans Serif

Requirements
Must have
• Wix Website
Clean fresh look with appropriate imaging
Web site is a company advertising that will hold static information and we will market through social media.
Nice to have
• Scientific look and feel
Should not have
• Prominent Corona Virus images or references

```html
<!DOCTYPE html>
<html lang="en">
<head>
<meta charset="utf-8">
<title>KLORVEST — We measure so you can Manage</title>
<link href="https://fonts.googleapis.com/css2?family=Poppins:wght@300;400;500;600;700&display=swap" rel="stylesheet">
<style>
:root{
  --orange:#f07a1c;
  --orange-deep:#d9600e;
  --orange-soft:#fbe3cf;
  --ink:#2b2b2b;
  --text:#8a8a8a;
  --line:#e3e3e3;
  --panel:#3b3b3d;
  --hero-dark:#151312;
  --footer:#1e1e20;
  --footer-text:#9a9a9a;
  --white:#ffffff;
}
*{box-sizing:border-box;margin:0;padding:0}
html,body{width:1200px;height:4200px;overflow:hidden}
body{font-family:'Poppins',sans-serif;color:var(--ink);background:var(--white);position:relative}
.section{position:absolute;left:0;width:1200px}
.heading{font-weight:600;font-size:30px;color:var(--orange);text-align:center;letter-spacing:.5px}
.lead{font-size:13px;line-height:22px;color:var(--text);text-align:center;width:720px;margin:0 auto}
.btn{display:block;background:var(--orange);color:var(--white);font-size:12px;font-weight:500;border-radius:20px;text-align:center}

/* header */
.site-header{position:absolute;top:0;left:0;width:1200px;height:80px;z-index:5;display:flex;align-items:center;padding:0 120px}
.brand{display:flex;align-items:center;gap:10px;color:var(--white);font-weight:600;font-size:20px;letter-spacing:1px}
.brand-dot{width:14px;height:14px;border-radius:50%;background:var(--orange)}
.main-nav{display:flex;gap:30px;margin-left:auto;font-size:13px;color:var(--white)}
.main-nav .active{color:var(--orange)}
.header-phone{display:flex;align-items:center;gap:8px;margin-left:60px;color:var(--white);font-size:14px;font-weight:500}

/* hero */
.hero{top:0;height:660px;background:var(--hero-dark)}
.hero-visual{position:absolute;inset:0;background:
  radial-gradient(circle at 67% 48%,#f7a15c 0,#e5741f 14%,rgba(180,80,20,.6) 26%,transparent 42%),
  radial-gradient(circle at 92% 20%,rgba(240,122,28,.8) 0,transparent 22%),
  radial-gradient(circle at 88% 82%,rgba(240,122,28,.55) 0,transparent 18%),
  linear-gradient(90deg,var(--hero-dark) 0,#2a1a10 35%,#5a2c0e 70%,#7a3a10 100%)}
.hero-copy{position:absolute;left:120px;top:210px;width:420px;color:var(--white)}
.hero-title{font-size:50px;font-weight:700;line-height:58px}
.hero-sub{font-size:14px;line-height:22px;margin-top:26px;width:320px}
.hero-dots{display:flex;gap:12px;margin-top:30px}
.hero-dots span{width:8px;height:8px;border-radius:50%;background:rgba(255,255,255,.6)}
.hero-dots span:first-child{background:var(--white)}

/* about */
.about{top:660px;height:400px;padding-top:118px}
.about .lead{margin-top:22px}
.about .btn{width:130px;height:38px;line-height:38px;margin:26px auto 0}

/* approach */
.approach{top:1060px;height:520px}
.approach-panel{position:absolute;left:0;top:0;width:600px;height:520px;background:linear-gradient(180deg,#434345 0,var(--panel) 60%,#323234 100%)}
.approach-photo{position:absolute;left:600px;top:0;width:600px;height:520px;background:
  radial-gradient(circle at 55% 35%,#f1c9a8 0,transparent 30%),
  linear-gradient(135deg,#e2761f 0,#f39a4e 40%,#f6efe8 70%,#d9d1c9 100%)}
.approach-copy{position:absolute;left:120px;top:190px;width:360px;color:var(--white)}
.approach-copy h2{font-size:30px;font-weight:600}
.approach-copy p{font-size:12px;line-height:20px;margin-top:18px;color:#d6d6d6}

/* services */
.services{top:1580px;height:1020px;padding-top:70px}
.services .lead{margin-top:18px}
.measure-box{position:absolute;left:230px;top:200px;width:740px;height:130px;background:#f4f4f4;border-radius:65px;text-align:center;padding-top:42px}
.measure-icon{position:absolute;left:345px;top:-26px;width:50px;height:50px;border-radius:50%;background:var(--white);border:2px solid var(--orange);display:flex;align-items:center;justify-content:center}
.measure-box h3{font-size:14px;font-weight:600;color:var(--ink)}
.measure-box p{font-size:11px;color:var(--text);margin-top:8px}
.hub{position:absolute;left:450px;top:560px;width:300px;height:300px}
.hub-name{position:absolute;left:0;top:0;width:300px;height:300px;display:flex;align-items:center;justify-content:center;font-size:30px;font-weight:600;color:var(--ink);letter-spacing:1px}
.service-item{position:absolute;width:260px}
.service-item .ico{width:58px;height:58px;border-radius:50%;border:2px solid var(--orange);display:flex;align-items:center;justify-content:center;background:var(--white)}
.service-item h4{font-size:13px;font-weight:600;margin-top:12px}
.service-item p{font-size:11px;line-height:18px;color:var(--text);margin-top:6px}
.service-item.right{text-align:left}

/* areas */
.areas{top:2600px;height:460px;background:
  radial-gradient(circle at 20% 30%,rgba(255,190,130,.35) 0,transparent 30%),
  radial-gradient(circle at 85% 70%,rgba(160,60,10,.35) 0,transparent 35%),
  linear-gradient(135deg,var(--orange-deep) 0,var(--orange) 55%,#f39245 100%)}
.areas .heading{color:var(--white);padding-top:50px}
.area-card{position:absolute;top:90px;width:280px;height:280px;background:var(--white);box-shadow:0 6px 18px rgba(0,0,0,.18)}
.area-card .photo{height:150px}
.area-card h3{font-size:15px;font-weight:600;color:var(--orange);margin:22px 20px 0}
.area-card p{font-size:11px;line-height:18px;color:var(--text);margin:8px 20px 0}

/* contact */
.contact{top:3060px;height:640px;padding-top:115px}
.contact .lead{margin-top:18px}
.field{position:absolute;height:40px;border:1px solid var(--line);border-radius:20px;font-size:11px;color:#a5a5a5;padding:11px 20px}
.field.message{height:100px;border-radius:22px}
.contact .btn{position:absolute;left:490px;top:520px;width:220px;height:40px;line-height:40px}

/* footer */
.site-footer{top:3700px;height:500px;background:var(--footer);color:var(--footer-text)}
.footer-col{position:absolute;top:80px}
.footer-col h5{font-size:15px;font-weight:600;color:var(--white);margin-bottom:26px}
.contact-row{display:flex;gap:22px;align-items:flex-start;margin-bottom:30px;font-size:11px;line-height:18px}
.link-list{list-style:none;font-size:11px;line-height:26px}
.link-list li::before{content:"";display:inline-block;width:5px;height:5px;border-radius:50%;background:var(--orange);margin-right:12px;vertical-align:middle}
.footer-brand{position:absolute;left:900px;top:110px;text-align:center;width:160px}
.footer-brand .name{font-size:22px;font-weight:600;color:var(--white);letter-spacing:1px}
.socials{display:flex;gap:10px;justify-content:center;margin-top:18px}
.socials span{width:26px;height:26px;border-radius:50%;background:var(--white)}
.copyright{position:absolute;left:0;bottom:36px;width:1200px;text-align:center;font-size:10px;color:#5e5e60}
</style>
</head>
<body>

<header class="site-header">
  <div class="brand"><span class="brand-dot"></span>KLORVEST</div>
  <nav class="main-nav">
    <span class="active">Home</span><span>About</span><span>Our Approach</span><span>Our Services</span><span>Contact</span>
  </nav>
  <div class="header-phone">
    <svg width="16" height="16" viewBox="0 0 24 24"><path fill="#f07a1c" d="M6.6 10.8a15.1 15.1 0 0 0 6.6 6.6l2.2-2.2c.3-.3.7-.4 1-.2 1.1.4 2.3.6 3.6.6.6 0 1 .4 1 1V20c0 .6-.4 1-1 1A17 17 0 0 1 3 4c0-.6.4-1 1-1h3.5c.6 0 1 .4 1 1 0 1.3.2 2.5.6 3.6.1.3 0 .7-.2 1z"/></svg>
    555-210-4478
  </div>
</header>

<section class="section hero">
  <div class="hero-visual" role="img" aria-label="Glowing orange microscopic cells on a dark laboratory background"></div>
  <div class="hero-copy">
    <h1 class="hero-title">We measure so you can Manage</h1>
    <p class="hero-sub">Measure cleanliness of any surface and a value added disinfecting fogging surface.</p>
    <div class="hero-dots"><span></span><span></span><span></span></div>
  </div>
</section>

<section class="section about">
  <h2 class="heading">ABOUT COMPANY</h2>
  <p class="lead">Our team uses calibrated field instruments to measure how clean every surface really is, then turns each reading into clear reports. Owners see trends, track progress across sites and plan cleaning with confidence, backed by audits that repeat on a schedule that suits the business.</p>
  <span class="btn">Read More</span>
</section>

<section class="section approach">
  <div class="approach-panel" role="img" aria-label="Faded laboratory glassware on a dark grey background"></div>
  <div class="approach-photo" role="img" aria-label="Scientist in a white coat working at a microscope in a bright lab"></div>
  <div class="approach-copy">
    <h2>OUR APPROACH</h2>
    <p>We start with a baseline test of your site, then return on a set plan to compare results over time.</p>
    <p>Locations, Trending, Tracking and Randomised test plans ongoing audits will be made available.</p>
  </div>
</section>

<section class="section services">
  <h2 class="heading">OUR SERVICES</h2>
  <p class="lead">Accurate surface testing and fogging for homes, workplaces, vehicles and shared spaces, with results you can read at a glance.</p>

  <div class="measure-box">
    <div class="measure-icon">
      <svg width="24" height="24" viewBox="0 0 24 24" fill="none" stroke="#f07a1c" stroke-width="2"><circle cx="10" cy="10" r="6"/><path d="M15 15l6 6"/></svg>
    </div>
    <h3>WE MEASURE SO YOU CAN MANAGE</h3>
    <p>Clear readings, simple reports and a plan that keeps every space on track.</p>
  </div>

  <div class="hub">
    <svg width="300" height="300" viewBox="0 0 300 300">
      <circle cx="150" cy="150" r="146" fill="none" stroke="#f07a1c" stroke-width="1.5" stroke-dasharray="3 6"/>
      <circle cx="150" cy="150" r="118" fill="#ffffff" stroke="#e6e6e6" stroke-width="14"/>
      <circle cx="150" cy="4" r="5" fill="#f07a1c"/>
      <circle cx="150" cy="296" r="5" fill="#f07a1c"/>
      <circle cx="4" cy="150" r="5" fill="#f07a1c"/>
      <circle cx="296" cy="150" r="5" fill="#f07a1c"/>
    </svg>
    <div class="hub-name">KLORVEST</div>
  </div>

  <div class="service-item" style="left:170px;top:520px">
    <div class="ico"><svg width="28" height="28" viewBox="0 0 24 24" fill="none" stroke="#f07a1c" stroke-width="1.6"><path d="M3 11l9-7 9 7"/><path d="M5 10v10h14V10"/><rect x="10" y="14" width="4" height="6"/></svg></div>
    <h4>RESIDENTIAL</h4>
    <p>Peace of mind for family homes with tested and treated living areas.</p>
  </div>
  <div class="service-item right" style="left:800px;top:520px">
    <div class="ico"><svg width="28" height="28" viewBox="0 0 24 24" fill="none" stroke="#f07a1c" stroke-width="1.6"><rect x="4" y="3" width="10" height="18"/><rect x="14" y="9" width="6" height="12"/><path d="M7 7h4M7 11h4M7 15h4"/></svg></div>
    <h4>COMMERCIAL</h4>
    <p>Offices and shops kept to a measured standard your staff can trust.</p>
  </div>
  <div class="service-item" style="left:170px;top:760px">
    <div class="ico"><svg width="28" height="28" viewBox="0 0 24 24" fill="none" stroke="#f07a1c" stroke-width="1.6"><rect x="5" y="3" width="14" height="15" rx="2"/><path d="M5 11h14"/><circle cx="8.5" cy="14.5" r="1"/><circle cx="15.5" cy="14.5" r="1"/><path d="M7 18v3M17 18v3"/></svg></div>
    <h4>TRANSPORTATION</h4>
    <p>Buses, vans and fleets checked between runs and fogged when needed.</p>
  </div>
  <div class="service-item right" style="left:800px;top:760px">
    <div class="ico"><svg width="28" height="28" viewBox="0 0 24 24" fill="none" stroke="#f07a1c" stroke-width="1.6"><path d="M6 8v8M18 8v8M3 10v4M21 10v4M6 12h12"/></svg></div>
    <h4>GYMS</h4>
    <p>Equipment, mats and change rooms tested so members train with ease.</p>
  </div>
</section>

<section class="section areas" aria-label="Areas we serve">
  <h2 class="heading">AREAS WE SERVE</h2>
  <div class="area-card" style="left:148px">
    <div class="photo" role="img" aria-label="Hands working on a laptop in an office" style="background:linear-gradient(135deg,#8aa3b8,#d7dfe6)"></div>
    <h3>COMMERCIAL</h3>
    <p>Tested and treated to a clear, measured standard.</p>
  </div>
  <div class="area-card" style="left:460px">
    <div class="photo" role="img" aria-label="Warmly lit modern living room" style="background:linear-gradient(135deg,#5a3a22,#e3a265)"></div>
    <h3>RESIDENTIAL</h3>
    <p>Tested and treated to a clear, measured standard.</p>
  </div>
  <div class="area-card" style="left:772px">
    <div class="photo" role="img" aria-label="Lab technician testing samples" style="background:linear-gradient(135deg,#c9ced6,#f2f2f2)"></div>
    <h3>TRANSPORTATION</h3>
    <p>Tested and treated to a clear, measured standard.</p>
  </div>
</section>

<section class="section contact">
  <h2 class="heading">CONTACT FORM</h2>
  <p class="lead">Leave your details and we will arrange a free site visit and test plan.</p>
  <div class="field" style="left:192px;top:240px;width:390px">Name</div>
  <div class="field" style="left:618px;top:240px;width:390px">Email</div>
  <div class="field" style="left:192px;top:305px;width:390px">Phone</div>
  <div class="field" style="left:618px;top:305px;width:390px">Subject</div>
  <div class="field message" style="left:192px;top:375px;width:816px">Message</div>
  <span class="btn">Submit Now</span>
</section>

<footer class="section site-footer">
  <div class="footer-col" style="left:160px">
    <h5>Get in Touch</h5>
    <div class="contact-row">
      <svg width="20" height="20" viewBox="0 0 24 24" fill="none" stroke="#9a9a9a" stroke-width="1.6"><rect x="3" y="5" width="18" height="14" rx="1"/><path d="M3 6l9 7 9-7"/></svg>
      <div>info@klorvest.com<br>help@klorvest.com</div>
    </div>
    <div class="contact-row">
      <svg width="20" height="20" viewBox="0 0 24 24" fill="none" stroke="#9a9a9a" stroke-width="1.6"><rect x="7" y="2" width="10" height="20" rx="2"/><path d="M11 18h2"/></svg>
      <div>+00 555 210 4478<br>+00 555 210 4479</div>
    </div>
    <div class="contact-row">
      <svg width="20" height="20" viewBox="0 0 24 24" fill="none" stroke="#9a9a9a" stroke-width="1.6"><path d="M12 22s7-7 7-12a7 7 0 0 0-14 0c0 5 7 12 7 12z"/><circle cx="12" cy="10" r="2.5"/></svg>
      <div>14 Harbour Lane,<br>Eastfield 4102</div>
    </div>
  </div>
  <div class="footer-col" style="left:430px">
    <h5>Quick Links</h5>
    <ul class="link-list"><li>About Us</li><li>Blog</li><li>Contact us</li><li>FAQ</li><li>Insurance</li><li>Privacy</li></ul>
  </div>
  <div class="footer-col" style="left:640px">
    <h5>Our Services</h5>
    <ul class="link-list"><li>Residential</li><li>Commercial</li><li>Transportation</li><li>Gyms</li><li>Educational &amp; Daycare</li><li>Real Estate</li></ul>
  </div>
  <div class="footer-brand">
    <div class="name">KLORVEST</div>
    <div class="socials"><span></span><span></span></div>
  </div>
  <p class="copyright">© 2024 KLORVEST. All rights reserved.</p>
</footer>

</body>
</html>
```